Brintel Works - Fast, Efficient and Gas Mainteance for Domestic, Commercial and Industrial clients

We are in the process of purchasing a new business and would like to get a new logo and business card.
Business is a gas maintenance business that also does new gas installations.
Has been established since 1988.
Services include:
Install all types of gas appliances & equipment inc. hot water units
Maintain / repair / replace all types of gas appliances & equipment

Target Market(s)

Domestic, Commercial and Industrial clients

Industry/Entity Type

Business

Contact Information for Business Card

admin@brintelworks.com.au
07 3918 4726
Brintel Works PTY LTD

Logo Text

Gas Fitting & Plumbing Maintenance Specialists

Font styles to use
Sans Serif

Requirements
Must have
• Logo
• Business name, contact number, email address, web address
• Domestic | Commercial | Industrial Est Since 1988
Nice to have
• Possibly a black card with a flame logo to one side
Should not have
• Spelling errors

```html
<!DOCTYPE html>
<html lang="en">
<head>
<meta charset="utf-8">
<title>Brintel Works Business Card</title>
<link href="https://fonts.googleapis.com/css2?family=Merriweather:wght@400;700&family=Open+Sans:wght@300;400;600;700&family=Great+Vibes&display=swap" rel="stylesheet">
<style>
  :root {
    --stage: #e8e5e1;
    --card-white: #f5f5f4;
    --flame: #ef6e4f;
    --flame-deep: #d9533a;
    --flame-light: #f4845f;
    --ink: #44444f;
    --ink-soft: #7a7a84;
    --mark-grey: #cfcfcf;
    --on-flame: #ffffff;
  }
  * { box-sizing: border-box; margin: 0; padding: 0; }
  html, body {
    width: 1200px; height: 892px; overflow: hidden;
    background: var(--stage);
  }
  .canvas {
    width: 1200px; height: 892px;
    display: flex; align-items: center; justify-content: center; gap: 40px;
  }
  .card {
    position: relative; width: 540px; height: 309px;
    border-radius: 4px; overflow: hidden;
    box-shadow: 0 10px 24px rgba(0,0,0,.18);
  }
  .card-front { background: var(--card-white); }
  .card-front .sweep { position: absolute; inset: 0; }

  .identity { position: absolute; left: 36px; top: 72px; }
  .company-name {
    font-family: "Merriweather", serif; font-weight: 700;
    font-size: 26px; color: var(--flame); letter-spacing: .3px;
    text-transform: uppercase; line-height: 1; white-space: nowrap;
  }
  .company-name .legal {
    font-family: "Open Sans", sans-serif; font-size: 6px; font-weight: 600;
    color: var(--flame); vertical-align: top; margin-left: 3px; letter-spacing: .5px;
  }
  .tagline {
    font-family: "Open Sans", sans-serif; font-weight: 700;
    font-size: 14px; color: var(--ink); margin-top: 6px; white-space: nowrap;
  }
  .sectors {
    display: flex; align-items: baseline; gap: 10px; margin-top: 3px; white-space: nowrap;
  }
  .sectors .list {
    font-family: "Open Sans", sans-serif; font-size: 8.5px; color: var(--ink-soft);
  }
  .sectors .established {
    font-family: "Great Vibes", cursive; font-size: 15px; color: var(--ink-soft);
  }
  .brand-dot {
    position: absolute; left: 40px; top: 212px;
    width: 58px; height: 58px; border-radius: 50%; background: var(--mark-grey);
  }

  .contact {
    position: absolute; right: 38px; top: 148px; text-align: right;
    font-family: "Open Sans", sans-serif; color: var(--on-flame); white-space: nowrap;
  }
  .contact .phone { font-size: 18px; font-weight: 400; letter-spacing: .5px; }
  .contact .email, .contact .web { font-size: 15px; font-weight: 400; margin-top: 12px; }
  .contact .web { margin-top: 2px; }

  .contact-icons {
    position: absolute; right: 38px; top: 98px; display: flex; gap: 14px;
  }
  .contact-icons svg { width: 16px; height: 16px; display: block; }

  .card-back {
    background: linear-gradient(135deg, var(--flame-light) 0%, var(--flame) 50%, var(--flame-deep) 100%);
  }
  .back-brand {
    position: absolute; left: 60px; top: 50%; transform: translateY(-50%);
    display: flex; align-items: center; gap: 16px;
  }
  .back-brand .dot {
    width: 40px; height: 40px; border-radius: 50%; background: var(--on-flame);
  }
  .back-brand .name {
    font-family: "Merriweather", serif; font-weight: 700; font-size: 30px;
    color: var(--on-flame); text-transform: uppercase; letter-spacing: .5px;
  }
</style>
</head>
<body>
<main class="canvas">
  <section class="card card-front" aria-label="Business card front">
    <svg class="sweep" viewBox="0 0 540 309" preserveAspectRatio="none" aria-hidden="true">
      <defs>
        <linearGradient id="sweepFill" x1="0" y1="0" x2="1" y2="1">
          <stop offset="0" stop-color="#f4845f"/>
          <stop offset=".6" stop-color="#ef6e4f"/>
          <stop offset="1" stop-color="#d9533a"/>
        </linearGradient>
      </defs>
      <path d="M540 50 Q 330 110 150 309 L540 309 Z" fill="url(#sweepFill)"/>
    </svg>

    <div class="identity">
      <h1 class="company-name">Brintel Works<span class="legal">PTY LTD</span></h1>
      <p class="tagline">Gas fitting &amp; Plumbing Specialists</p>
      <p class="sectors">
        <span class="list">Domestic | Commercial | Industrial</span>
        <span class="established">Est Since 1988</span>
      </p>
    </div>
    <div class="brand-dot" aria-hidden="true"></div>

    <div class="contact-icons" aria-hidden="true">
      <svg viewBox="0 0 16 16"><rect width="16" height="16" rx="2" fill="#fff"/><path d="M5 3.5l2 2-1 1.2c.6 1.4 1.7 2.5 3.1 3.1l1.2-1 2 2-1.3 1.7C7.5 12.3 3.7 8.5 3.5 4.8z" fill="#ef6e4f"/></svg>
      <svg viewBox="0 0 16 16"><rect width="16" height="16" rx="2" fill="#fff"/><rect x="3" y="4.5" width="10" height="7" fill="none" stroke="#ef6e4f" stroke-width="1.2"/><path d="M3 4.5l5 4 5-4" fill="none" stroke="#ef6e4f" stroke-width="1.2"/></svg>
      <svg viewBox="0 0 16 16"><rect width="16" height="16" rx="2" fill="#fff"/><circle cx="8" cy="8" r="4.8" fill="none" stroke="#ef6e4f" stroke-width="1.2"/><path d="M3.2 8h9.6M8 3.2c-2.4 2.6-2.4 7 0 9.6M8 3.2c2.4 2.6 2.4 7 0 9.6" fill="none" stroke="#ef6e4f" stroke-width="1"/></svg>
    </div>

    <div class="contact">
      <p class="phone">07 3918 4726</p>
      <p class="email">admin@brintelworks.com.au</p>
      <p class="web">www.brintelworks.com.au</p>
    </div>
  </section>

  <section class="card card-back" aria-label="Business card back">
    <div class="back-brand">
      <span class="dot" aria-hidden="true"></span>
      <span class="name">Brintel Works</span>
    </div>
  </section>
</main>
</body>
</html>
```